Quorva - corporate Business Card

We need a good look and innovative business card for a new start up company based in Los Angeles called "Quorva". We are in a payment business, including payment card, app, and ewallet. We are expert in online payment and Card not present (CNP) transaction.
We need an innovative, modern business card.

Our logo font is Aero Matics

Target Market(s)

Startup - Bank - Online Payment - Card Manufacturing

Industry/Entity Type

Startup

Contact Information for Business Card

phone: 555 014 7396 - Address: 4172 Marlowe blvd, Larkhaven, CA 90299

Requirements
Must have
• Message: innovative, professional, expert, high tech, trust, online payment expert, security
Nice to have
• no comment
Should not have
• no Comment

```html
<!DOCTYPE html>
<html lang="en">
<head>
<meta charset="utf-8">
<title>Quorva — Business Card</title>
<link rel="stylesheet" href="https://fonts.googleapis.com/css2?family=Fira+Sans:wght@400;500&display=swap">
<style>
  :root {
    --backdrop: #1d1d1e;
    --brand-red: #b71f2e;
    --paper: #ffffff;
    --ink-light: #ffffff;
  }
  * { margin: 0; padding: 0; box-sizing: border-box; }
  html, body {
    width: 1200px; height: 987px; overflow: hidden;
    background: var(--backdrop);
    font-family: "Fira Sans", Arial, sans-serif;
  }
  .canvas { position: relative; width: 1200px; height: 987px; }

  .card {
    position: absolute;
    width: 615px; height: 352px;
    background: var(--paper);
    overflow: hidden;
  }
  .card--front { left: 293px; top: 130px; }
  .card--back  { left: 292px; top: 505px; }

  .contact-panel {
    position: absolute; left: 0; top: 0;
    width: 296px; height: 100%;
    background: var(--brand-red);
    color: var(--ink-light);
  }
  .holder-name {
    position: absolute; left: 24px; top: 67px;
    font-size: 21px; font-weight: 500; line-height: 26px;
  }
  .holder-role {
    position: absolute; left: 23px; top: 95px;
    font-size: 16px; font-weight: 400; line-height: 20px;
  }
  .address {
    position: absolute; left: 24px; top: 161px;
    font-size: 15px; line-height: 20px; font-style: normal;
  }
  .contact-list {
    position: absolute; left: 24px; top: 213px;
    list-style: none; font-size: 15px;
  }
  .contact-list li {
    display: flex; align-items: center; height: 23px;
  }
  .contact-list svg { width: 16px; height: 16px; margin-right: 10px; fill: var(--ink-light); }

  .brand-mark {
    position: absolute;
    display: flex; align-items: center;
    color: var(--brand-red);
    font-weight: 500;
    letter-spacing: 1px;
  }
  .brand-mark__dot {
    border-radius: 50%;
    background: var(--brand-red);
    flex: none;
  }
  .card--front .brand-mark { left: 268px; top: 132px; font-size: 58px; }
  .card--front .brand-mark__dot {
    width: 86px; height: 86px; margin-right: 12px;
    border: 2px solid var(--paper);
  }
  .card--back .brand-mark { left: 118px; top: 119px; font-size: 75px; }
  .card--back .brand-mark__dot { width: 114px; height: 114px; margin-right: 16px; }
</style>
</head>
<body>
<main class="canvas">
  <section class="card card--front" aria-label="Business card front">
    <div class="contact-panel">
      <div class="holder-name">Marcus Hale</div>
      <div class="holder-role">President</div>
      <address class="address">4172 Marlowe blvd<br>Larkhaven, CA 90299</address>
      <ul class="contact-list">
        <li>
          <svg viewBox="0 0 16 16" aria-hidden="true"><path d="M1 5c0-2 3-3 7-3s7 1 7 3v1h-3V4.5H4V6H1z"/><path d="M3 7h10l1 7H2z M8 8.5a2 2 0 1 0 0.01 0z"/></svg>
          555 014 7396
        </li>
        <li>
          <svg viewBox="0 0 16 16" aria-hidden="true"><path d="M1 3h14v1.2L8 9 1 4.2z"/><path d="M1 5.8 8 10.6l7-4.8V13H1z"/></svg>
          marcus@quorva.com
        </li>
        <li>
          <svg viewBox="0 0 16 16" aria-hidden="true"><circle cx="8" cy="8" r="7"/><path d="M5 4c2 1 1 3 3 3s1 3 0 4-1 2-1 3" stroke="#b71f2e" stroke-width="1.4" fill="none"/></svg>
          www.quorva.com
        </li>
      </ul>
    </div>
    <div class="brand-mark">
      <span class="brand-mark__dot" aria-hidden="true"></span>
      <span class="brand-mark__name">quorva</span>
    </div>
  </section>

  <section class="card card--back" aria-label="Business card back">
    <div class="brand-mark">
      <span class="brand-mark__dot" aria-hidden="true"></span>
      <span class="brand-mark__name">quorva</span>
    </div>
  </section>
</main>
</body>
</html>
```